Brightwave Charters website

Looking to have a new, interactive website built on Wordpress and hosted by hostorra. Our current site was made and is hosted by plim and has been up and running for 8 years. Would like to replace as seamlessly as possible. Attached are general ideas for the site as well as requirements. Would like to showcase our charter options and information on the home page with Our Charters, FAQ and Gallery as follow up pages. Would like to be created in Wordpress and HTTPS

Target Market(s)

Vacationing tourists visiting Siesta Key

Industry/Entity Type

Boat Charters

Number of Pages Required

1 page

Requirements
Must have
• Website must be secure, HTTPS not HTTP . . Use webp images throughout the entire site. Info for the home page was uploaded on 3 seperate pages labeled home1, home2 and home3. Need the bottom, above footer, to show What Our Customers Say About Us with reviews from Plentora, Zentrix and QM. Homepage to have all 6 charter options and info provided on the attached docx labeled home1, home2 and home3 . If we can get the 3 pages following the home page (Our Charters,FAQ and Gallery) I had also attached brief summaries for those pages. Install these Plug-ins, MERV, Slotwise (free), Blockforge plugin. Any other plugin needs to be approved by us

```html
<!DOCTYPE html>
<html lang="en">
<head>
<meta charset="utf-8">
<title>Brightwave Charters — Private Boat Tours on Siesta Key</title>
<link href="https://fonts.googleapis.com/css2?family=Cinzel:wght@500;600&family=Lato:wght@400;700;900&display=swap" rel="stylesheet">
<style>
:root{
  --navy:#16286a;
  --navy-deep:#0f1f55;
  --blue:#1e4a9a;
  --sky:#bfe0f6;
  --sky-soft:#e6f2fb;
  --orange:#e0661c;
  --orange-dark:#c9500f;
  --ink:#1d1d2b;
  --text:#2d2d35;
  --muted:#6b6f7a;
  --white:#ffffff;
  --card-shadow:0 4px 14px rgba(20,30,70,.16);
}
*{box-sizing:border-box;margin:0;padding:0}
html,body{width:1200px;height:4934px;overflow:hidden}
body{position:relative;font-family:"Lato",sans-serif;color:var(--text);background:var(--white)}
.abs{position:absolute}
.heading{font-family:"Cinzel",serif;font-weight:600;text-align:center;color:var(--ink);letter-spacing:1px}
.heading-rule{width:92px;height:4px;background:var(--orange);border-radius:2px;margin:0 auto}
.btn{display:inline-flex;align-items:center;justify-content:center;background:linear-gradient(180deg,#ea7428,var(--orange-dark));color:#fff;font-weight:900;font-size:15px;border-radius:26px;letter-spacing:.3px}

/* header */
.topbar{left:494px;top:0;width:706px;height:44px;background:linear-gradient(90deg,var(--navy-deep),var(--blue));border-bottom-left-radius:40px;display:flex;align-items:center;padding-left:46px;gap:16px;color:#fff;font-size:15px;font-weight:700}
.topbar .sep{opacity:.8}
.topbar svg{width:14px;height:14px;fill:var(--orange);margin-right:8px;vertical-align:-2px}
.social-row{display:flex;gap:8px;margin-left:14px}
.social-row span{width:28px;height:28px;border-radius:50%;background:#fff}
.social-row span.on{background:var(--orange)}
.logo-badge{left:108px;top:-20px;width:196px;height:216px;border-radius:0 0 98px 98px;background:#fff;display:flex;align-items:center;justify-content:center;z-index:3}
.logo-name{font-family:"Lato",sans-serif;font-weight:900;font-size:24px;line-height:1.1;color:var(--navy);text-align:center;margin-top:30px}
.nav{left:398px;top:82px;display:flex;gap:0;font-weight:900;font-size:15px;color:var(--ink)}
.nav a{color:inherit;text-decoration:none;margin-right:38px}
.nav a.active{color:var(--orange);border-bottom:2px solid var(--orange)}
.nav-cta{left:942px;top:72px;width:146px;height:46px}

/* hero */
.hero{left:0;top:140px;width:1200px;height:620px;overflow:hidden}
.hero-photo{position:absolute;inset:0;background:linear-gradient(180deg,#9ec6e4 0%,#b6d4e8 26%,#4a78a8 34%,#2d5a8e 60%,#24507f 100%)}
.hero-title{left:0;top:198px;width:1200px;font-family:"Cinzel",serif;font-weight:600;font-size:52px;line-height:56px;color:#fff;text-align:center;text-shadow:0 2px 6px rgba(0,0,0,.35)}
.hero-arrow{width:44px;height:44px;border-radius:50%;background:rgba(20,30,60,.55);top:250px;display:flex;align-items:center;justify-content:center}
.hero-arrow svg{width:16px;height:16px;stroke:#fff;stroke-width:3;fill:none}
.hero-dots{left:546px;top:516px;display:flex;gap:13px}
.hero-dots i{width:16px;height:16px;border-radius:50%;background:#fff}
.hero-dots i.on{background:var(--orange);box-shadow:0 0 0 3px #fff}
.hero-wave{left:0;top:520px;width:1200px;height:240px}

/* charters */
.options-title{left:0;top:858px;width:1200px;font-size:50px}
.options-rule{left:554px;top:918px}
.card{width:305px;height:345px;background:#fff;border-radius:12px;box-shadow:var(--card-shadow);border:1px solid #eef0f4}
.card.featured{border:2px solid #f0a36a}
.card-photo{position:absolute;left:8px;top:8px;width:289px;height:212px;border-radius:8px}
.card-icon{position:absolute;left:106px;top:172px;width:92px;height:92px;border-radius:50%;background:radial-gradient(circle at 40% 35%,#2a66b8,var(--navy));border:5px solid #fff;display:flex;align-items:center;justify-content:center}
.card.featured .card-icon{background:radial-gradient(circle at 40% 35%,#f08a3e,var(--orange-dark))}
.card-icon svg{width:44px;height:44px;fill:none;stroke:#fff;stroke-width:2.6;stroke-linecap:round;stroke-linejoin:round}
.card-label{position:absolute;left:0;top:296px;width:100%;text-align:center;font-weight:700;font-size:17px;color:var(--ink);letter-spacing:.2px}

/* booking band */
.book-band{left:0;top:1840px;width:1200px;height:980px}
.book-title{left:0;top:1992px;width:1200px;font-size:43px;line-height:48px;color:#fff}
.book-rule{left:554px;top:2096px}
.price-list{left:112px;top:2130px;list-style:none;color:#fff;font-size:22px;font-weight:700;line-height:39.5px}
.price-list li::before{content:"";display:inline-block;width:7px;height:7px;border-radius:50%;background:var(--orange);margin:0 24px 4px 0;vertical-align:middle}
.book-copy{left:112px;top:2298px;width:490px;color:#fff;font-size:15.5px;line-height:25px}
.book-cta{left:112px;top:2578px;width:154px;height:46px}
.book-photo{left:636px;top:2152px;width:454px;height:454px;border-radius:50%;border:6px solid #d7ecfb;background:linear-gradient(180deg,#9cc9ec 0%,#5e9ccc 38%,#e9d8c4 60%,#3a5b8f 100%)}

/* about */
.about-title{left:0;top:2890px;width:1200px;font-size:48px}
.about-intro{left:110px;top:2980px;width:980px;text-align:center;font-size:15.5px;line-height:25px;color:var(--text)}
.about-ring{left:110px;top:3196px;width:446px;height:446px;border-radius:50%;background:var(--sky-soft)}
.about-photo{left:142px;top:3228px;width:382px;height:382px;border-radius:50%;background:linear-gradient(180deg,#c8dcec 0%,#a9c6da 42%,#7fb0a4 60%,#5e8f86 100%)}
.about-copy{left:616px;top:3196px;width:474px;text-align:justify;font-size:15.5px;line-height:24.6px;color:var(--text)}
.about-copy p+p{margin-top:14px}

/* reviews */
.reviews-band{left:0;top:3700px;width:1200px;height:880px}
.reviews-title{left:0;top:3988px;width:1200px;font-size:50px;line-height:54px;color:#fff}
.reviews-rule{left:554px;top:4096px}
.review{width:310px;height:254px;background:#fff;border-radius:10px;top:4102px;padding:16px 16px 0}
.review-head{display:flex;align-items:center;gap:10px;font-size:20px;font-weight:700;color:var(--ink);padding-bottom:12px;border-bottom:1px solid #e2e4ea}
.review-head i{width:26px;height:26px;border-radius:50%;background:var(--navy)}
.review-head i.sq{border-radius:4px}
.stars{color:#2bb673;font-size:15px;letter-spacing:2px}
.stars.gold{color:#f2b01e}
.reviewer{display:flex;gap:12px;margin-top:14px;align-items:flex-start}
.avatar{width:44px;height:44px;border-radius:50%;background:#d6d8de;color:#777;font-weight:700;display:flex;align-items:center;justify-content:center;flex:none}
.reviewer b{display:block;font-size:15px;color:var(--ink)}
.reviewer b.link{color:#3b5fb0}
.reviewer small{font-size:12px;color:var(--muted)}
.review-text{font-size:13px;line-height:20.5px;color:var(--muted);margin-top:10px}
.review-sub{font-size:15px;font-weight:700;color:var(--ink);margin-top:4px}

/* footer */
.footer{left:0;top:4560px;width:1200px;height:374px;background:linear-gradient(180deg,#ffffff,#f1f7fc)}
.footer-logo{left:116px;top:4640px;width:200px;font-family:"Lato",sans-serif;font-weight:900;font-size:28px;line-height:1.15;color:var(--navy);text-align:center}
.footer-logo .mark{width:60px;height:60px;border-radius:50%;background:var(--navy);margin:0 auto 12px}
.col-title{font-size:17px;font-weight:700;color:var(--ink);letter-spacing:.4px}
.links{left:434px;top:4606px}
.links ul{list-style:none;margin-top:18px}
.links li{font-size:14px;color:var(--text);line-height:38px;display:flex;align-items:center;gap:16px}
.links li::before{content:"";width:13px;height:13px;border-radius:50%;background:var(--orange)}
.contact{left:656px;top:4606px}
.contact-row{display:flex;gap:16px;margin-top:18px}
.contact-row svg{width:13px;height:15px;fill:var(--orange);flex:none;margin-top:2px}
.contact-row b{display:block;font-size:14px;color:var(--ink);font-weight:700}
.contact-row span{font-size:12.5px;color:var(--text);line-height:22px}
.follow{left:982px;top:4606px}
.follow-row{display:flex;align-items:center;gap:12px;margin-top:14px;font-size:12.5px;line-height:16px;color:var(--text)}
.follow-row i{width:28px;height:28px;border-radius:50%;background:#fde7d9;flex:none}
.follow-row i.on{background:var(--orange)}
.footer-line{left:114px;top:4884px;width:974px;height:1px;background:#d5dbe4}
.copyright{left:0;top:4898px;width:1200px;text-align:center;font-size:12px;color:var(--text)}
</style>
</head>
<body>

<!-- Header -->
<div class="abs topbar">
  <span><svg viewBox="0 0 24 24"><path d="M6.6 10.8a15.1 15.1 0 006.6 6.6l2.2-2.2c.3-.3.7-.4 1-.2 1.1.4 2.3.6 3.6.6.6 0 1 .4 1 1V20c0 .6-.4 1-1 1A17 17 0 013 4c0-.6.4-1 1-1h3.5c.6 0 1 .4 1 1 0 1.3.2 2.5.6 3.6.1.3 0 .7-.2 1z"/></svg>555-014-2290</span>
  <span class="sep">|</span>
  <span><svg viewBox="0 0 24 24"><path d="M2 5h20v14H2z M2 5l10 8 10-8" /></svg>hello@brightwavecharters.com</span>
  <div class="social-row"><span class="on"></span><span></span><span></span><span></span></div>
</div>
<div class="abs logo-badge"><div class="logo-name">Brightwave<br>Charters</div></div>
<nav class="abs nav">
  <a class="active" href="#">HOME</a><a href="#">OUR CHARTERS</a><a href="#">FAQ</a><a href="#">GALLERY</a><a href="#">CONTACT</a>
</nav>
<a class="abs btn nav-cta" href="#">BOOK NOW</a>

<!-- Hero -->
<section class="abs hero">
  <div class="hero-photo" role="img" aria-label="Photo of a white motorboat speeding across the bay off Siesta Key"></div>
  <h1 class="abs hero-title">BEST PRIVATE BOAT TOUR<br>ON SIESTA KEY</h1>
  <div class="abs hero-arrow" style="left:20px"><svg viewBox="0 0 16 16"><path d="M10 2L4 8l6 6"/></svg></div>
  <div class="abs hero-arrow" style="left:1136px"><svg viewBox="0 0 16 16"><path d="M6 2l6 6-6 6"/></svg></div>
  <div class="abs hero-dots"><i></i><i class="on"></i><i></i><i></i></div>
</section>
<svg class="abs hero-wave" viewBox="0 0 1200 240" preserveAspectRatio="none">
  <path d="M0 120 C260 260 560 230 800 150 C960 98 1100 70 1200 84 L1200 240 L0 240Z" fill="#1a3577"/>
  <path d="M0 132 C260 256 560 236 800 172 C960 128 1100 110 1200 118 L1200 240 L0 240Z" fill="#3d72b8"/>
  <path d="M0 150 C250 262 560 250 810 196 C970 160 1100 146 1200 150 L1200 240 L0 240Z" fill="#ffffff"/>
</svg>

<!-- Charter options -->
<h2 class="abs heading options-title">CHARTER OPTIONS</h2>
<div class="abs heading-rule options-rule"></div>

<div class="abs card" style="left:111px;top:963px">
  <div class="card-photo" role="img" aria-label="Photo of a dolphin leaping beside the boat" style="background:linear-gradient(180deg,#9cc6e2,#3c7fb8 45%,#2a5d94)"></div>
  <div class="card-icon"><svg viewBox="0 0 44 44"><circle cx="22" cy="22" r="14"/><path d="M22 4v8M22 32v8M4 22h8M32 22h8M18 26l8-8"/></svg></div>
  <div class="card-label">DOLPHIN/WILDLIFE TOURS</div>
</div>
<div class="abs card featured" style="left:448px;top:963px">
  <div class="card-photo" role="img" aria-label="Photo of guests floating together at a sandbar" style="background:linear-gradient(180deg,#5aa6e2,#9ed8ea 45%,#63c2c7)"></div>
  <div class="card-icon"><svg viewBox="0 0 44 44"><path d="M10 34h24M14 34l4-14h8l4 14M30 8l-8 14"/></svg></div>
  <div class="card-label">SANDBAR FUN</div>
</div>
<div class="abs card" style="left:784px;top:963px">
  <div class="card-photo" role="img" aria-label="Photo of a snorkeler swimming in clear green water" style="background:linear-gradient(180deg,#8fb79c,#6f9f8a 50%,#93b8a0)"></div>
  <div class="card-icon"><svg viewBox="0 0 44 44"><rect x="8" y="14" width="24" height="12" rx="6"/><path d="M36 8v18a8 8 0 01-8 8h-4"/></svg></div>
  <div class="card-label">SNORKELING</div>
</div>
<div class="abs card" style="left:111px;top:1333px">
  <div class="card-photo" role="img" aria-label="Photo of a beach covered in seashells" style="background:linear-gradient(180deg,#7fb6e4,#a9cfe3 35%,#cdb9a1 60%,#9e8b78)"></div>
  <div class="card-icon"><svg viewBox="0 0 44 44"><path d="M8 28a14 14 0 0128 0zM22 28V14M15 28l4-13M29 28l-4-13M14 34h16"/></svg></div>
  <div class="card-label">SHELLING &amp; BEACHES</div>
</div>
<div class="abs card" style="left:448px;top:1333px">
  <div class="card-photo" role="img" aria-label="Photo of friends smiling together at a waterfront tiki bar" style="background:linear-gradient(180deg,#8fbbe0,#6f8d6e 45%,#4d4a4a)"></div>
  <div class="card-icon"><svg viewBox="0 0 44 44"><rect x="12" y="8" width="20" height="28" rx="9"/><path d="M16 18h4M24 18h4M17 28h10"/></svg></div>
  <div class="card-label">TIKI BAR CRAWL</div>
</div>
<div class="abs card" style="left:784px;top:1333px">
  <div class="card-photo" role="img" aria-label="Photo of a red sun setting over the water behind a boat" style="background:linear-gradient(180deg,#b8877f,#a8736c 45%,#6d5450)"></div>
  <div class="card-icon"><svg viewBox="0 0 44 44"><path d="M12 24a10 10 0 0120 0M22 6v5M8 14l3 3M36 14l-3 3M6 30c5-3 9 3 16 0s11 3 16 0M10 36c4-2 8 2 12 0s8 2 12 0"/></svg></div>
  <div class="card-label">SUNSET CRUISE</div>
</div>

<!-- Booking band -->
<svg class="abs book-band" viewBox="0 0 1200 980" preserveAspectRatio="none" role="img" aria-label="Deep blue background with a faint photo of the bay at dusk">
  <defs>
    <linearGradient id="bandFill" x1="0" y1="0" x2="0" y2="1">
      <stop offset="0" stop-color="#1f3a86"/><stop offset="1" stop-color="#122a72"/>
    </linearGradient>
  </defs>
  <path d="M0 60 C200 150 450 110 720 40 C920 -8 1080 0 1200 40 L1200 180 L0 180Z" fill="#bfe0f6"/>
  <path d="M0 92 C220 170 470 130 730 70 C930 28 1080 34 1200 66 L1200 900 C1060 860 900 840 720 880 C500 930 250 970 0 900Z" fill="url(#bandFill)"/>
  <path d="M0 900 C250 970 500 930 720 880 C900 840 1060 860 1200 900 L1200 980 L0 980Z" fill="#ffffff"/>
  <path d="M720 880 C900 840 1060 860 1200 900 L1200 920 C1060 884 900 868 730 906Z" fill="#bfe0f6"/>
</svg>
<h2 class="abs heading book-title">BOOK YOUR SIESTA KEY BOAT<br>CHARTER TODAY!</h2>
<div class="abs heading-rule book-rule"></div>
<ul class="abs price-list">
  <li>2 Hours- $300 + tax</li>
  <li>3 Hours- $425 + tax</li>
  <li>4 Hours- $550 + tax</li>
  <li>Additional hours $125/Hr + tax</li>
</ul>
<p class="abs book-copy">Depart from Siesta Key and enjoy your day on our roomy 25 ft Tidecraft 25SC Deck Boat. There is ample space for everyone to sit comfortably and maneuver around the boat on your private charter for up to 6 people. With the Bimini top up, there is plenty of shaded seating. &nbsp;There is an open bow and lounge seat in the back for the sun worshipers. The boat is equipped with a bluetooth stereo system, so you can listen to your favorite music. There is plenty of cooler space and we provide the extra ice, bottled water, light snacks and all the gear for a fun day. &nbsp;You are welcome to bring your own food and drinks.</p>
<a class="abs btn book-cta" href="#">BOOK NOW</a>
<div class="abs book-photo" role="img" aria-label="Photo of a smiling family seated aboard the boat"></div>

<!-- About -->
<h2 class="abs heading about-title">ABOUT US</h2>
<div class="abs heading-rule" style="left:554px;top:2952px;display:none"></div>
<p class="abs about-intro">Welcome to the BEST private charter on and around Siesta Key! Whether you live on Siesta Key, &nbsp;Sarasota or are one of our many welcome visitors... we want you to enjoy the day on the crystal clear waters and pristine beaches. &nbsp;My name is Dan Reyes and I look forward to being your Captain for the day. My goal is to ensure a safe and fun time on the water. &nbsp;I will work hard to create unforgettable memories with a charter that you, your family and friends will remember. &nbsp;I have been boating since the age of 13 and am a USCG licensed Master Captain. &nbsp;We will take your private party of up to 6 people, out from 2 hours up to a full 8 hour day charter. So many options for your day. You can choose from our specific charters or build your own. Just let us know what your perfect day on the water includes. Feel free to call/text/email us anytime if you would like suggestions or have questions.</p>
<div class="abs about-ring"></div>
<div class="abs about-photo" role="img" aria-label="Photo of the charter deck boat with a canopy top resting on green water"></div>
<div class="abs about-copy">
  <p>You will depart from Siesta Key and enjoy your day on our roomy 25 ft Tidecraft 25SC Deck Boat. There is ample space for everyone to sit comfortably and maneuver around the boat on your private charter. With the Bimini top up, there is plenty of shaded seating. There is an open bow and lounge seat in the back for the sun worshipers. The boat is equipped with a bluetooth stereo system, so you can listen to your favorite music. There is also a portable head and fresh water rinsing station to wash away the saltwater. There is plenty of cooler space and we provide the extra ice, bottled water, light snacks and all the gear for a fun day. You are welcome to bring your own food and drinks.</p>
  <p>There are many fun options to choose from for your fun day on the water. &nbsp;We will customize the day for you to make sure it is the perfect boat charter. Our most popular charter times are 2 or 4 hours but we always try to be flexible depending on availability. &nbsp;We will happily have you out for up to a fun filled, full 8 hour day. You tell us what time frame works best for you!</p>
</div>

<!-- Reviews -->
<svg class="abs reviews-band" viewBox="0 0 1200 880" preserveAspectRatio="none" role="img" aria-label="Deep blue background with a faint photo of fishing rods over the water">
  <defs>
    <linearGradient id="revFill" x1="0" y1="0" x2="0" y2="1">
      <stop offset="0" stop-color="#1b3278"/><stop offset="1" stop-color="#122766"/>
    </linearGradient>
  </defs>
  <path d="M0 80 C220 20 470 10 720 70 C920 118 1080 110 1200 60 L1200 160 L0 160Z" fill="#bfe0f6"/>
  <path d="M0 110 C230 50 470 44 720 100 C930 148 1080 140 1200 96 L1200 760 C1040 830 860 850 620 800 C400 756 200 770 0 830Z" fill="url(#revFill)"/>
  <path d="M0 830 C200 770 400 756 620 800 C860 850 1040 830 1200 760 L1200 880 L0 880Z" fill="#ffffff"/>
</svg>
<h2 class="abs heading reviews-title">WHAT OUR CHARTER GUESTS<br>HAVE TO SAY ABOUT US</h2>
<div class="abs heading-rule reviews-rule"></div>

<article class="abs review" style="left:111px">
  <div class="review-head"><i></i>Plentora Reviews</div>
  <div class="stars" style="margin-top:14px">★★★★★</div>
  <div class="review-sub">Down time and Dolphins</div>
  <p class="review-text" style="margin-top:4px">Dan took my husband and I out for an afternoon to decompress from hurricane cleanup and evacuation.. His boat was immaculate and very comfortable for an afternoon cruise to Venice .</p>
</article>
<article class="abs review" style="left:444px">
  <div class="review-head"><i></i>Zentrix Reviews</div>
  <div class="reviewer"><div class="avatar">R</div><div><b>Name Heading</b><span class="stars gold">★★★★★</span></div></div>
  <p class="review-text">Dan took my husband and I out for an afternoon to decompress from hurricane cleanup and evacuation.. His boat was immaculate and very comfortable for an afternoon cruise to Venice .</p>
</article>
<article class="abs review" style="left:778px">
  <div class="review-head"><i class="sq"></i>QM Reviews</div>
  <div class="reviewer"><div class="avatar"></div><div><b class="link">Name Heading</b><small>2 days ago</small></div></div>
  <p class="review-text">Dan took my husband and I out for an afternoon to decompress from hurricane cleanup and evacuation.. His boat was immaculate and very comfortable for an afternoon cruise to Venice .</p>
</article>

<!-- Footer -->
<footer class="abs footer"></footer>
<div class="abs footer-logo"><div class="mark"></div>Brightwave<br>Charters</div>
<div class="abs links">
  <div class="col-title">QUICK LINKS</div>
  <ul><li>Home</li><li>Our Charters</li><li>FAQ</li><li>Gallery</li><li>Contact</li></ul>
</div>
<div class="abs contact">
  <div class="col-title">CONTACT INFO</div>
  <div class="contact-row"><svg viewBox="0 0 12 16"><path d="M6 0a6 6 0 00-6 6c0 4.5 6 10 6 10s6-5.5 6-10a6 6 0 00-6-6zm0 8.5A2.5 2.5 0 116 3.5a2.5 2.5 0 010 5z"/></svg><div><b>DEPARTURE ADDRESS:</b><span>1420 Harbor Light Way, Siesta Key</span></div></div>
  <div class="contact-row"><svg viewBox="0 0 24 24"><path d="M6.6 10.8a15.1 15.1 0 006.6 6.6l2.2-2.2c.3-.3.7-.4 1-.2 1.1.4 2.3.6 3.6.6.6 0 1 .4 1 1V20c0 .6-.4 1-1 1A17 17 0 013 4c0-.6.4-1 1-1h3.5c.6 0 1 .4 1 1 0 1.3.2 2.5.6 3.6.1.3 0 .7-.2 1z"/></svg><div><b>PHONE:</b><span>555-014-2290</span></div></div>
  <div class="contact-row"><svg viewBox="0 0 24 24"><path d="M2 4h20v16H2zM4 6l8 6 8-6v-.5H4z" fill-rule="evenodd"/></svg><div><b>EMAIL:</b><span>hello@brightwavecharters.com</span></div></div>
</div>
<div class="abs follow">
  <div class="col-title">FOLLOW US</div>
  <div class="follow-row"><i></i><span>Follow Us on<br>QM</span></div>
  <div class="follow-row"><i></i><span>Follow Us on<br>CHIRPER</span></div>
  <div class="follow-row"><i class="on"></i><span>Follow Us on<br>SNAPGRID</span></div>
  <div class="follow-row"><i></i><span>Follow Us on<br>Localo</span></div>
</div>
<div class="abs footer-line"></div>
<div class="abs copyright">© 2024 BRIGHTWAVE CHARTERS &nbsp;| &nbsp;All Rights Reserved</div>

</body>
</html>
```